Business Card Design for Training Business

Clear Path Coaching is a new business that delivers training and other services with a focus on topics related to mental health and wellbeing, for example, Wellmind Response Course, Resilience etc. We have a strong focus on evidence-based psychology and neuroscience. I have a logo which I will upload with the brief, so please consider colours that work well with the logo.
Target Market(s)
Adults, workplaces (particularly government and not-for-profits)
Industry/Entity Type
Business
Contact Information for Business Card
Head Strong TrainingSamantha SellwoodDirector0438 770 850sam@headstrongtraining.com.auwww.headstrongtraining.com.au

```html
<!DOCTYPE html>
<html lang="en">
<head>
<meta charset="utf-8">
<title>Clear Path Coaching – Business Card</title>
<link rel="stylesheet" href="https://fonts.googleapis.com/css2?family=Open+Sans:wght@300;400;600&display=swap">
<style>
  :root {
    --page: #ecebe8;
    --card: #ffffff;
    --ink: #111111;
    --brand-grey: #6b6664;
    --teal: #4bbcc4;
    --teal-soft: #bfe6e8;
    --ornament: #7d7a78;
    --ornament-light: #e4e2e0;
  }
  * { box-sizing: border-box; margin: 0; padding: 0; }
  html, body {
    width: 1200px; height: 960px; overflow: hidden;
    background: var(--page);
    font-family: "Open Sans", sans-serif;
  }
  .card {
    position: absolute; left: 80px; top: 183px;
    width: 1040px; height: 594px;
    background: var(--card);
    overflow: hidden;
    box-shadow: 0 6px 24px rgba(0,0,0,0.15);
  }
  .brand {
    position: absolute; left: 60px; top: 110px; width: 400px;
    text-align: center; color: var(--brand-grey); font-weight: 300;
  }
  .brand-mark {
    display: block; width: 150px; height: 150px; margin: 0 auto 26px;
    border-radius: 50%;
    background: radial-gradient(circle, #ffffff 0%, var(--teal-soft) 45%, var(--teal) 100%);
  }
  .brand-name { font-size: 44px; letter-spacing: 5px; line-height: 1.1; }
  .brand-sub { font-size: 20px; letter-spacing: 10px; margin-top: 8px; }
  .divider {
    position: absolute; left: 520px; top: 150px;
    width: 3px; height: 300px; background: var(--teal);
  }
  .contact {
    position: absolute; right: 40px; top: 110px;
    text-align: right; color: var(--ink);
  }
  .contact-name { font-size: 36px; font-weight: 600; line-height: 1.15; }
  .contact-role { font-size: 24px; font-weight: 600; margin-bottom: 22px; }
  .contact-line {
    display: flex; justify-content: flex-end; align-items: center; gap: 10px;
    font-size: 25px; line-height: 1.35;
  }
  .contact-icon { width: 22px; height: 22px; flex: none; }
  .ornament-band {
    position: absolute; left: 0; bottom: 0; width: 100%; height: 120px;
    background: linear-gradient(to top, var(--ornament) 0%, var(--ornament-light) 60%, var(--card) 100%);
    opacity: 0.55;
  }
</style>
</head>
<body>
  <main class="card">
    <div class="brand">
      <span class="brand-mark"></span>
      <div class="brand-name">CLEAR PATH</div>
      <div class="brand-sub">COACHING</div>
    </div>

    <div class="divider"></div>

    <div class="contact">
      <div class="contact-name">Rebecca Tanfield</div>
      <div class="contact-role">Director</div>
      <div class="contact-line">0491 362 517
        <svg class="contact-icon" viewBox="0 0 22 22" aria-hidden="true"><rect width="22" height="22" fill="#111"/><path d="M7 4c1 0 2 3 2 4s-1 1-1 2 3 5 4 5 1-1 2-1 4 1 4 2-2 3-3 3C9 19 3 13 3 7c0-1 2-3 4-3z" fill="#fff"/></svg>
      </div>
      <div class="contact-line">bec@clearpathcoaching.example.au
        <svg class="contact-icon" viewBox="0 0 22 22" aria-hidden="true"><rect width="22" height="22" fill="#111"/><rect x="4" y="6" width="14" height="10" fill="none" stroke="#fff" stroke-width="1.6"/><path d="M4 6l7 6 7-6" fill="none" stroke="#fff" stroke-width="1.6"/></svg>
      </div>
      <div class="contact-line">www.clearpathcoaching.example.au
        <svg class="contact-icon" viewBox="0 0 22 22" aria-hidden="true"><rect width="22" height="22" fill="#111"/><circle cx="11" cy="11" r="7" fill="none" stroke="#fff" stroke-width="1.6"/><path d="M4 11h14M11 4c-3 4-3 10 0 14M11 4c3 4 3 10 0 14" fill="none" stroke="#fff" stroke-width="1.2"/></svg>
      </div>
    </div>

    <div class="ornament-band" role="img" aria-label="Row of grey line-work mandala half-circles along the bottom edge"></div>
  </main>
</body>
</html>
```